Single brochure for international companies in the financial sector

We need to update a brochure 4 pages presenting our company. We are a financial engineering company. The final design must provide financial security, service and trust. you will find the current brochure copy. Our color code is Orange (RGB 235/100/68), Black, White and Gray. photos show the visual of the site, but it is not mandatory to keep them.

Target Market(s)

wealth management professionals

Industry/Entity Type

Finance

Requirements
Must have
• Logo Corvelle Capital all text in the document color Orange Corvelle (RGB 235/100/68)
Nice to have
• Vista Font
Should not have
• images / pictures of people

```html
<!DOCTYPE html>
<html lang="en">
<head>
<meta charset="utf-8">
<title>Corvelle Capital — Brochure</title>
<link rel="stylesheet" href="https://fonts.googleapis.com/css2?family=Lora:ital,wght@0,400;0,700;1,400&display=swap">
<style>
  :root {
    --orange: #eb6444;
    --ink: #1c1c1c;
    --paper: #f7f7f7;
    --paper-shade: #eeeeee;
    --gray-bg: #d6d6d6;
    --photo-light: #d2d2d2;
    --photo-mid: #9a9a9a;
    --photo-dark: #3a3a3a;
    --text-gray: #444444;
  }
  * { box-sizing: border-box; margin: 0; padding: 0; }
  html, body {
    width: 1200px; height: 2308px; overflow: hidden;
    background: var(--gray-bg);
    font-family: "Lora", Georgia, serif;
    color: var(--ink);
  }
  .canvas { position: relative; width: 1200px; height: 2308px; }

  /* Cover page (front cover, used standalone and in outside spread) */
  .cover {
    position: absolute;
    width: var(--page); height: var(--page);
    font-size: calc(var(--page) / 40);
    background: var(--paper);
    overflow: hidden;
  }
  .cover__masthead {
    height: 22em; padding: 0 3em;
    display: flex; flex-direction: column;
    align-items: center; justify-content: center; text-align: center;
  }
  .brand-name {
    font-family: "Lora", Georgia, serif; font-weight: 400;
    color: var(--ink); text-transform: uppercase; line-height: 1;
    white-space: nowrap;
  }
  .brand-name__main { display: block; font-size: 2.2em; letter-spacing: .3em; margin-right: -.3em; }
  .brand-name__sub { display: block; font-size: 1.3em; letter-spacing: .36em; margin-right: -.36em; margin-top: .55em; }
  .cover__rule { width: 13em; height: 1px; background: var(--ink); margin: 1.3em 0 1em; }
  .cover__tagline {
    font-size: .62em; letter-spacing: .3em; text-transform: uppercase; color: var(--text-gray);
  }
  .cover__photo {
    height: 18em;
    background: linear-gradient(180deg, var(--photo-light) 0%, #bdbdbd 45%, var(--photo-mid) 62%, var(--photo-dark) 78%, #8c8c8c 100%);
  }

  /* Spreads */
  .spread {
    position: absolute; left: 40px; width: 1120px; height: 560px;
    display: flex; box-shadow: 0 18px 40px rgba(0,0,0,.18);
  }
  .page { position: relative; width: 560px; height: 560px; background: var(--paper); }
  .page--left { background: linear-gradient(90deg, var(--paper) 85%, var(--paper-shade)); }
  .page--right { background: linear-gradient(90deg, var(--paper-shade), var(--paper) 15%); }

  /* Inside left: the company */
  .company { position: absolute; left: 115px; top: 120px; width: 330px; text-align: center; }
  .company__title { font-size: 34px; font-weight: 400; letter-spacing: .06em; text-transform: uppercase; }
  .company__rule { height: 1px; background: var(--ink); margin: 10px 20px 14px; }
  .company__quote { font-size: 40px; line-height: .6; color: #bbbbbb; }
  .company__lead { font-size: 13px; font-weight: 700; line-height: 1.5; margin: 8px 0 20px; }
  .label { font-size: 10px; letter-spacing: .35em; text-transform: uppercase; margin: 16px 0 6px; }
  .copy { font-size: 12.5px; line-height: 1.6; color: var(--text-gray); }
  .copy--accent { color: var(--orange); font-size: 15px; }

  /* Inside right: services */
  .services { position: absolute; left: 50px; top: 70px; width: 460px; text-align: center; }
  .services__cols { display: flex; margin: 26px 0; }
  .services__col { flex: 1; padding: 0 18px; }
  .services__divider { width: 1px; background: var(--ink); }

  /* Outside spread */
  .back { background: var(--orange); }
  .back__legal {
    position: absolute; left: 70px; bottom: 56px;
    font-size: 10.5px; letter-spacing: .22em; line-height: 1.9;
    color: var(--paper); text-transform: uppercase; text-align: center;
  }
</style>
</head>
<body>
<main class="canvas">

  <section class="cover" style="--page: 700px; left: 250px; top: 60px;" aria-label="Front cover">
    <div class="cover__masthead">
      <h1 class="brand-name">
        <span class="brand-name__main">Corvelle</span>
        <span class="brand-name__sub">Capital</span>
      </h1>
      <div class="cover__rule"></div>
      <p class="cover__tagline">Financial Engineering</p>
    </div>
    <div class="cover__photo" role="img" aria-label="Black and white photograph of a long arched viaduct reflected in still water"></div>
  </section>

  <section class="spread" style="top: 860px;" aria-label="Inside spread">
    <article class="page page--left">
      <div class="company">
        <h2 class="company__title">The Company.</h2>
        <div class="company__rule"></div>
        <div class="company__quote">&ldquo;</div>
        <p class="company__lead">Our clients must deliver performance on their portfolios on a regular basis.<br>We help them deliver everyday.</p>
        <h3 class="label">About us</h3>
        <p class="copy">Corvelle Capital is a financial engineering company.<br>It is fully independent from any bank or any other company.</p>
        <h3 class="label">What we do</h3>
        <p class="copy">We provide them with investment solutions designed to improve their portfolio performance.</p>
        <p class="copy copy--accent">Simple as that.</p>
      </div>
    </article>
    <article class="page page--right">
      <div class="services">
        <h3 class="label">Our clients</h3>
        <p class="copy">Our clients are financial professionals such as wealth managers, institutionals, corporates and family offices. Our purpose is to help them reach their goals every day.</p>
        <div class="services__cols">
          <div class="services__col">
            <h3 class="label">Investment advice</h3>
            <p class="copy">Each client is unique. We listen to their needs and design tailored products with clear terms, fair pricing and steady support.</p>
          </div>
          <div class="services__divider"></div>
          <div class="services__col">
            <h3 class="label">Portfolio analysis</h3>
            <p class="copy">We review our clients' portfolios and their financial products, identify the needs for hedging or reallocating assets, and provide full reporting services over the life of the products.</p>
          </div>
        </div>
        <h3 class="label">Partner selection</h3>
        <p class="copy">Our internal tools allow us to compare the issuers we are working with. We give our clients the best terms for their investment solutions.</p>
      </div>
    </article>
  </section>

  <section class="spread" style="top: 1560px;" aria-label="Outside spread">
    <article class="page back">
      <p class="back__legal">
        Corvelle Capital SA, capital :<br>
        400 000 euros<br>
        RCS Paris : 512 448 903<br>
        Code Banque (CIB) : 14720<br>
        www.corvellecapital.com
      </p>
    </article>
    <section class="cover" style="--page: 560px; position: relative;" aria-label="Front cover">
      <div class="cover__masthead">
        <h2 class="brand-name">
          <span class="brand-name__main">Corvelle</span>
          <span class="brand-name__sub">Capital</span>
        </h2>
        <div class="cover__rule"></div>
        <p class="cover__tagline">Financial Engineering</p>
      </div>
      <div class="cover__photo" role="img" aria-label="Black and white photograph of a long arched viaduct reflected in still water"></div>
    </section>
  </section>

</main>
</body>
</html>
```